Harvest Gateway Fellowship Ministries needs a fresh new web design

We are an up and coming multicultural church that aims to bring people into a life changing encounter with God. We need a fresh and inviting website in order to increase our internet presence and make us easier to connect with.
Here are some of the basic requirements for the site:
• Clearly displayed address, service times, and contact info
• A staff profile page
• An area for a calendar with upcoming events and their details
• Social media buttons
• Group pages for the different ministries (youth, children’s church, men, etc…)
• An area for donations and eCommerce
• A resources page for assorted media (podcasts, sermons, videos, etc.…)
• An area for prayer requests.

```html
<!DOCTYPE html>
<html lang="en">
<head>
<meta charset="utf-8">
<title>Harvest Gateway Fellowship Ministries – Events</title>
<link rel="stylesheet" href="https://fonts.googleapis.com/css2?family=Lato:wght@300;400;700&display=swap">
<style>
:root{
  --royal:#1d1196;
  --royal-footer:#1e0f94;
  --gold:#e5c20f;
  --gold-text:#e0b90a;
  --ink:#555;
  --ink-dark:#4a4a4a;
  --muted:#777;
  --page:#f3f3f3;
  --rule:#d6d6d6;
  --icon:#b9b9b9;
  --footer-text:#c9c6ee;
}
*{box-sizing:border-box;margin:0;padding:0}
html,body{width:1181px;height:1200px;overflow:hidden}
body{font-family:'Lato',sans-serif;color:var(--ink);background:var(--page);position:relative}
.wrap{position:absolute;left:98px;width:985px}

.topbar{position:absolute;top:0;left:0;width:1181px;height:39px;background:var(--royal);color:#fff}
.topbar .tagline{position:absolute;left:98px;top:12px;font-size:12.5px}
.topbar .schedule-label{position:absolute;left:724px;top:12px;font-size:13px}
.topbar .schedule{position:absolute;left:906px;top:6px;border-left:2px solid #fff;padding-left:10px;font-size:11px;line-height:14px}

.header{position:absolute;top:39px;left:0;width:1181px;height:114px;background:#fff}
.brand{position:absolute;left:98px;top:18px;width:242px;height:74px;display:flex;align-items:center;gap:8px}
.brand-dot{width:44px;height:44px;border-radius:50%;background:var(--royal);flex:none}
.brand-name{font-size:16px;font-weight:700;color:var(--royal);line-height:18px}
.info{position:absolute;top:24px;text-align:right;font-size:13.5px;line-height:15px;color:var(--ink)}
.info h3{font-size:15px;font-weight:700;color:#555;margin-bottom:5px}
.info a{display:block;color:var(--gold-text);font-size:11.5px;text-decoration:none;margin-top:3px}
.info-sep{position:absolute;top:28px;width:2px;height:62px;background:#ddd}
.header .social{position:absolute;left:1056px;top:29px}
.social span{display:block;width:27px;height:27px;border-radius:50%;background:var(--icon);margin-bottom:4px}

.nav{position:absolute;top:153px;left:0;width:1181px;height:40px;background:var(--gold);border-top:2px solid #d9b40a}
.nav ul{list-style:none;display:flex;position:absolute;left:98px;top:10px;font-size:14px;color:#3b3b3b}
.nav li{padding:0 25px 0 16px;border-right:1px solid #c9a80a;line-height:16px}
.nav li:last-child{border:0}

.hero{position:absolute;top:193px;left:0;width:1181px;height:98px;background:linear-gradient(90deg,#4a3410,#6e5218 35%,#5a4112 60%,#3c2a0c)}
.crumbs{position:absolute;left:98px;top:27px;font-size:13px;color:#eee}
.crumbs b{color:#fff;font-weight:700}
.hero h1{position:absolute;left:98px;top:44px;font-size:25px;font-weight:700;color:#fff}

.article{position:absolute;left:108px;top:345px;width:620px}
.article h2{font-size:24px;font-weight:700;color:#5a5a5a}
.article .date{font-size:13px;color:var(--muted);margin:1px 0 12px}
.article p{font-size:13px;line-height:20px;color:#6a6a6a;margin-bottom:19px}
.article hr{border:0;border-top:1px solid var(--rule);margin-top:25px}
.share{display:flex;align-items:center;gap:8px;margin-top:20px;font-size:13px;color:#555}
.share span{width:25px;height:25px;border-radius:50%;background:#cfcfcf}
.share .label{width:auto;height:auto;background:none;margin-right:4px}

.upcoming{position:absolute;left:778px;top:345px;width:306px}
.upcoming h2{font-size:24px;font-weight:300;color:var(--gold-text);width:295px;border-bottom:1px solid #bbb;padding-bottom:4px}
.event{padding:23px 0 10px;border-bottom:1px dashed #ddd}
.event + .event{padding-top:8px}
.event .day{font-size:30px;line-height:30px;color:var(--gold-text)}
.event .day b{font-weight:700}
.event .day span{font-weight:300;margin-left:6px}
.event h3{font-size:19px;font-weight:700;color:#555;margin:1px 0 4px}
.event p{font-size:13px;line-height:20px;color:#777}
.event:last-child{border:0}

.footer{position:absolute;top:903px;left:0;width:1181px;height:297px;background:var(--royal-footer);color:var(--footer-text)}
.fcol{position:absolute;top:40px;font-size:13px;line-height:18px}
.fcol h4{font-size:19px;font-weight:400;color:#fff;margin-bottom:11px;text-transform:uppercase}
.fcol ul{list-style:none}
.fcol li{line-height:24px}
.contact-line{display:flex;align-items:center;gap:9px;font-size:14px;margin-top:2px;line-height:20px}
.email-input{width:224px;height:34px;background:#fff;border:1px solid #ddd;border-radius:3px;margin-top:9px;color:#aaa;font-size:13px;padding:9px 12px}
.subscribe{display:inline-block;margin-top:10px;background:var(--gold);color:#fff;font-size:13px;padding:8px 19px;border-radius:2px}
.fsocial{display:flex;gap:8px;margin-top:12px}
.fsocial span{width:32px;height:32px;border-radius:50%;background:#9a96d3}
.copyright{position:absolute;left:98px;top:221px;width:985px;border-top:1px solid #3a2fa6;text-align:center;padding-top:16px;font-size:11.5px;letter-spacing:.3px}
</style>
</head>
<body>

<div class="topbar">
  <div class="tagline">A house of prayer for all nations, where the love, the presence and the power of God are real.</div>
  <div class="schedule-label">SUNDAY SERVICE SCHEDULE</div>
  <div class="schedule">09:00 A.M. | Sunday School<br>10:30 A.M. | Convergent Service</div>
</div>

<header class="header">
  <div class="brand"><span class="brand-dot"></span><span class="brand-name">Harvest Gateway Fellowship Ministries</span></div>
  <div class="info" style="right:619px"><h3>Donate</h3>Lorem Ipsum is simply<br>dummy text of the printing<a>Donate Now »</a></div>
  <div class="info-sep" style="left:583px"></div>
  <div class="info" style="right:341px"><h3>Request Prayer</h3>Lorem Ipsum is simply dummy text<br>of the printing and typesetting industry.<a>Request Now »</a></div>
  <div class="info-sep" style="left:860px"></div>
  <div class="info" style="right:166px"><h3>Address</h3>Harvest Gateway<br>City, Location<a>Contact »</a></div>
  <div class="info-sep" style="left:1034px"></div>
  <div class="social"><span></span><span></span></div>
</header>

<nav class="nav">
  <ul>
    <li>Home</li><li>About</li><li>Staff Profile</li><li>News and Events</li><li>Worship &amp; Services</li><li>Groups</li><li>Shop</li><li>Resources</li><li>Contact</li>
  </ul>
</nav>

<section class="hero" role="img" aria-label="Warm golden wheat field photograph">
  <div class="crumbs">Home &gt; News and Events &gt; <b>Events</b></div>
  <h1>Events</h1>
</section>

<article class="article">
  <h2>Vacation Bible School</h2>
  <div class="date">July 31 - Aug 05 2014</div>
  <p>Lorem Ipsum is simply dummy text of the printing and typesetting industry. Lorem Ipsum has been the industry's standard dummy text ever since the 1500s, when an unknown printer took a galley of type and scrambled it to make a type specimen book It has survived not only five centuries.</p>
  <p>Also the leap into electronic typesetting, remaining essentially unchanged. It was popularised in the 1960s with the release of Lettermark sheets containing Lorem Ipsum passages, and more recently with desktop publishing software like Pagecraft Studio including versions of Lorem Ipsum.</p>
  <p>There are many variations of passages of Lorem Ipsum available, but the majority have suffered alteration in some form, by injected humour, or randomised words which don't look even slightly believable. If you are going to use a passage of Lorem Ipsum, you need to be sure there isn't anything embarrassing hidden.</p>
  <hr>
  <div class="share"><span class="label">Share</span><span></span><span></span></div>
</article>

<aside class="upcoming">
  <h2>UPCOMING EVENTS</h2>
  <div class="event"><div class="day"><b>29</b><span>JUL</span></div><h3>Vacation Bible School</h3><p>Lorem Ipsum is simply dummy text of the printing and typesetting industry.</p></div>
  <div class="event"><div class="day"><b>20</b><span>JUL</span></div><h3>Vacation Bible School</h3><p>Lorem Ipsum is simply dummy text of the printing and typesetting industry.</p></div>
  <div class="event"><div class="day"><b>28</b><span>JUN</span></div><h3>Vacation Bible School</h3><p>Lorem Ipsum is simply dummy text of the printing and typesetting industry.</p></div>
  <div class="event"><div class="day"><b>19</b><span>JUN</span></div><h3>Family and Friends Day</h3><p>Sunday June 29th is our family and friends day with special guest pastor Daniel Mercer. Come with faith..</p></div>
</aside>

<footer class="footer">
  <div class="fcol" style="left:98px">
    <h4>Contact Us</h4>
    Harvest Gateway<br>Location, city<br>State Name, Country
    <div class="contact-line" style="margin-top:12px">
      <svg width="15" height="15" viewBox="0 0 24 24"><path fill="#c9c6ee" d="M6.6 10.8a15 15 0 0 0 6.6 6.6l2.2-2.2c.3-.3.7-.4 1-.2 1.1.4 2.3.6 3.6.6.6 0 1 .4 1 1V20c0 .6-.4 1-1 1A17 17 0 0 1 3 4c0-.6.4-1 1-1h3.5c.6 0 1 .4 1 1 0 1.3.2 2.5.6 3.6.1.3 0 .7-.2 1z"/></svg>
      +1 555-014-2290</div>
    <div class="contact-line">
      <svg width="15" height="12" viewBox="0 0 24 18"><rect x="1" y="1" width="22" height="16" fill="none" stroke="#c9c6ee" stroke-width="2"/><path d="M1 1l11 9 11-9" fill="none" stroke="#c9c6ee" stroke-width="2"/></svg>
      hello@harvestgateway.org</div>
  </div>
  <div class="fcol" style="left:316px">
    <h4>Communities We Serve</h4>
    <div style="display:flex;gap:20px">
      <ul><li>• Lorem Ipsum</li><li>• Dummy Links</li><li>• More dummy</li><li>• Sample Text</li><li>• More samples</li></ul>
      <ul><li>• type text dummy</li><li>• Lorem Ipsum</li></ul>
    </div>
  </div>
  <div class="fcol" style="left:590px">
    <h4>Newsletter</h4>
    Enter your email below to get notified
    <div class="email-input">Your Email</div>
    <span class="subscribe">Subscribe</span>
  </div>
  <div class="fcol" style="left:863px;width:225px">
    <h4>Connect With Us</h4>
    Stay connected for the latest updates at Harvest Gateway Fellowship
    <div class="fsocial"><span></span><span></span></div>
  </div>
  <div class="copyright">Copyright © 2014. All rights reserved. Harvest Gateway.</div>
</footer>

</body>
</html>
```